Business Card Design

Printing and photocopying solutions, computer sales, photocopier sales and service, stationery needs

We aim to be the best for reliability, knowledge, skilled technical ability and highly ethical in business dealings. We would like to present as professional and the key person for dealing with for all customers. We are based in the Solomon Islands and therefore part of a developing country where many services and infrastructures are not in place. We would like to be seen as leading the field with technology and advanced office support. We strongly support the community and education systems with our current services and are seeking to expand the reach to encompass other service offerings

Target Market(s)

Business, Schools, Government offices, Churches, Non-government organisations

Industry/Entity Type

Business

Contact Information for Business Card

Harbourlight Print
harbourlightprint@mailvane.example
+677 7418062 +677 8205147
PO Box 8
Auki, Malaita Province
Solomon Islands

Requirements
Must have
• professional appearance. Some Blue colouring
Must have easy to read phone number so required the phone number to be large font

Must have Shop address as well
Shop 7, Tidewell Building
Auki, Malaita, Solomon Islands
Nice to have
• Keep simple and professional with appearance of the business card styles, use the back of the card for Logo and a list of the basic services that is offered from Harbourlight Print

```html
<!DOCTYPE html>
<html lang="en">
<head>
<meta charset="utf-8">
<title>Harbourlight Print – Business Card</title>
<link href="https://fonts.googleapis.com/css2?family=PT+Sans:wght@400;700&family=PT+Sans+Narrow:wght@700&display=swap" rel="stylesheet">
<style>
  :root {
    --backdrop: #e9e7e2;
    --card-white: #ffffff;
    --blue-deep: #1f4fb8;
    --ink: #2b2c30;
    --ink-soft: #55575c;
  }
  * { margin: 0; padding: 0; box-sizing: border-box; }
  html, body {
    width: 1200px;
    height: 1019px;
    overflow: hidden;
    background: var(--backdrop);
    font-family: "PT Sans", sans-serif;
  }
  .card {
    position: absolute;
    left: 75px;
    top: 210px;
    width: 1050px;
    height: 600px;
    border-radius: 6px;
    overflow: hidden;
    box-shadow: 0 14px 40px rgba(0,0,0,0.18);
    background: var(--card-white);
  }
  .card-shapes { position: absolute; inset: 0; }
  .brand {
    position: absolute;
    left: 175px;
    top: 270px;
    display: flex;
    align-items: center;
    gap: 16px;
  }
  .brand-mark {
    width: 22px;
    height: 22px;
    background: var(--blue-deep);
    flex: none;
  }
  .brand-name {
    color: var(--blue-deep);
    font-size: 42px;
    font-weight: 400;
    letter-spacing: 0.5px;
    white-space: nowrap;
  }
  .identity {
    position: absolute;
    right: 60px;
    top: 58px;
    text-align: right;
  }
  .person-name {
    font-family: "PT Sans Narrow", sans-serif;
    font-size: 44px;
    font-weight: 700;
    letter-spacing: 1px;
    color: var(--ink);
    line-height: 1;
  }
  .person-name .first { color: var(--blue-deep); }
  .person-role {
    font-size: 24px;
    color: var(--ink-soft);
    margin-top: 4px;
  }
  .contact-list {
    position: absolute;
    right: 60px;
    top: 190px;
    list-style: none;
    text-align: right;
  }
  .contact-item {
    display: flex;
    justify-content: flex-end;
    align-items: center;
    gap: 14px;
    font-size: 21px;
    color: var(--ink);
    height: 36px;
    white-space: nowrap;
  }
  .contact-item.phone { font-size: 25px; font-weight: 700; }
  .contact-icon { width: 20px; height: 20px; flex: none; }
</style>
</head>
<body>
  <article class="card">
    <svg class="card-shapes" viewBox="0 0 1050 600" width="1050" height="600" aria-hidden="true">
      <defs>
        <linearGradient id="greyCorner" x1="0" y1="0" x2="1" y2="1">
          <stop offset="0" stop-color="#c9cbcf"/>
          <stop offset="1" stop-color="#eceef1"/>
        </linearGradient>
        <linearGradient id="blueSweep" x1="0" y1="0" x2="1" y2="0">
          <stop offset="0" stop-color="#1c48b0"/>
          <stop offset="0.55" stop-color="#2f7fe6"/>
          <stop offset="1" stop-color="#1f4fb8"/>
        </linearGradient>
        <linearGradient id="charcoalBand" x1="0" y1="0" x2="1" y2="1">
          <stop offset="0" stop-color="#2c2d30"/>
          <stop offset="1" stop-color="#55575b"/>
        </linearGradient>
      </defs>
      <path d="M0 0 H380 C210 50 112 190 112 340 C112 440 160 520 240 575 L0 600 Z" fill="url(#greyCorner)"/>
      <path d="M0 330 C40 520 210 600 430 560 L1050 440 V600 H0 Z" fill="url(#blueSweep)"/>
      <path d="M0 450 C70 560 180 600 320 600 H0 Z" fill="url(#charcoalBand)"/>
      <path d="M520 600 C620 560 780 540 1050 520 V600 Z" fill="#1b44a6" opacity="0.55"/>
    </svg>

    <div class="brand">
      <span class="brand-mark"></span>
      <span class="brand-name">Harbourlight Print</span>
    </div>

    <header class="identity">
      <h1 class="person-name"><span class="first">DANIEL</span> KWAIGA</h1>
      <p class="person-role">Managing Director</p>
    </header>

    <ul class="contact-list">
      <li class="contact-item phone">+677 7418062
        <svg class="contact-icon" viewBox="0 0 20 20"><path d="M5 2 L8 2 L9 6 L7 8 C8 11 9 12 12 13 L14 11 L18 12 L18 15 C18 17 16 18 14 18 C8 17 3 12 2 6 C2 4 3 2 5 2 Z" fill="#1f4fb8"/></svg>
      </li>
      <li class="contact-item phone">+677 8205147
        <svg class="contact-icon" viewBox="0 0 20 20"><rect x="5" y="1" width="10" height="18" rx="2" fill="#1f4fb8"/><rect x="7" y="4" width="6" height="10" fill="#fff"/></svg>
      </li>
      <li class="contact-item">harbourlightprint@mailvane.example
        <svg class="contact-icon" viewBox="0 0 20 20"><rect x="1" y="4" width="18" height="12" rx="1.5" fill="#1f4fb8"/><path d="M2 5 L10 11 L18 5" stroke="#fff" stroke-width="1.5" fill="none"/></svg>
      </li>
      <li class="contact-item">www.harbourlightprint.example
        <svg class="contact-icon" viewBox="0 0 20 20"><circle cx="10" cy="10" r="8.5" fill="#1f4fb8"/><path d="M1.5 10 H18.5 M10 1.5 C6 6 6 14 10 18.5 M10 1.5 C14 6 14 14 10 18.5" stroke="#fff" stroke-width="1.2" fill="none"/></svg>
      </li>
      <li class="contact-item">Shop 7, Tidewell Building, Auki
        <svg class="contact-icon" viewBox="0 0 20 20"><path d="M10 19 C5 12 4 10 4 7.5 A6 6 0 0 1 16 7.5 C16 10 15 12 10 19 Z" fill="#1f4fb8"/><circle cx="10" cy="7.5" r="2.2" fill="#fff"/></svg>
      </li>
    </ul>
  </article>
</body>
</html>
```